QuillVane needs a dashboard page designed

Redesign the dashboard shown in the provided images.

There are two images:
- dashboard.png
- dashboard-expanded.png

NOTE: The vocabulary navigation on the left will be a very long list of words 100s, so keep that in mind when you're designing both the vocab navigation and the expanded vocab popup.

In the dashboard.png picture, there needs to be a progress chart showing the word progress like the following: review 1(show it as completed) -> review 2(show the user they are here) -> review 3(unvisited) -> review 4(unvisited)

The do-not-design-this-page.png image is for your reference only. It is not to be designed. Use it to understand the overall look and feel of the website to help you create the best dashboard page possible.
Updates

Need extra days to review

Industry/Entity Type

Education English learning

Number of Pages Required

1 page

Requirements
Must have
• The main navigation and main header cannot change between pages. See the do-not-design page for the main navigateion and header.
Should not have
• Do not add a person profile. We will not have images of our users. Keep the icons in the main navigation as they are.

```html
<!DOCTYPE html>
<html lang="en">
<head>
<meta charset="utf-8">
<title>WordNest Tutor Dashboard</title>
<link href="https://fonts.googleapis.com/css2?family=Poppins:wght@400;500;600;700&display=swap" rel="stylesheet">
<style>
:root{
  --side-top:#2c2236;--side-bot:#150b22;--ink:#16101f;--muted:#555;
  --purple:#6a4fc8;--purple-bg:#f1eefd;--orange:#f07a3f;--orange-bg:#fff2ea;
  --teal:#169fb8;--teal-bg:#eaf9fc;--gold:#f2b21d;--gold-bg:#fff1d2;
  --green:#7bbf3a;--line:#e3e3e3;
}
*{box-sizing:border-box;margin:0;padding:0}
html,body{width:1200px;height:844px;overflow:hidden;background:#fff;font-family:"Poppins",sans-serif;color:var(--ink)}
.sidebar{position:absolute;left:0;top:0;width:228px;height:844px;background:linear-gradient(180deg,var(--side-top),var(--side-bot) 40%);color:#fff}
.brand{position:absolute;left:30px;top:34px;font-size:21px;font-weight:700;letter-spacing:-.3px}
.brand-ext{position:absolute;left:184px;top:41px}
.nav-active{position:absolute;left:0;top:92px;width:196px;height:37px;background:#fff;border-radius:0 19px 19px 0;display:flex;align-items:center;justify-content:space-between;padding:0 18px 0 32px;color:var(--gold);font-size:12px;font-weight:600}
.filter{position:absolute;left:34px;top:144px;width:165px;border-bottom:1px solid #4a3f55;padding-bottom:10px;font-size:12px;display:flex;justify-content:space-between}
.group{position:absolute;left:34px;width:165px}
.group h3{font-size:13px;font-weight:600;display:flex;justify-content:space-between;align-items:center}
.group .sub{font-size:11px;color:#ddd}
.group .cur{font-size:11px;color:var(--green);font-weight:600}
.group ul{list-style:none;margin-top:6px}
.group li{font-size:11.5px;color:#9a8fb0;line-height:17.8px;margin-left:1px}
.qmark{width:15px;height:15px;border:1.3px solid #fff;border-radius:50%;font-size:9px;display:flex;align-items:center;justify-content:center;font-weight:500}
.extra{position:absolute;left:34px;display:flex;align-items:center;gap:9px;font-size:12.5px;font-weight:600}
.topbar{position:absolute;left:1052px;top:22px;display:flex;align-items:center;gap:8px}
.avatar{width:32px;height:32px;border-radius:50%;background:var(--gold);color:#fff;font-weight:700;font-size:17px;display:flex;align-items:center;justify-content:center;margin-left:6px}
.review{position:absolute;top:71px;width:222px;height:82px;border:1px solid;border-radius:6px;padding:16px 0 0 31px}
.review .lbl{font-size:11px}
.review .st{font-size:12px;font-weight:600;margin-top:2px}
.review .bar{width:118px;height:4px;border-radius:2px;background:#fff;margin-top:6px}
.review .bar i{display:block;height:4px;border-radius:2px}
.review .dot{position:absolute;right:21px;top:20px;width:42px;height:42px;border-radius:50%;background:#fff;display:flex;align-items:center;justify-content:center}
.r1{left:274px;background:var(--purple-bg);border-color:var(--purple)}
.r1 .st{color:var(--purple)}
.r2{left:501px;background:var(--orange-bg);border-color:var(--orange)}
.r2 .st{color:var(--orange)}
.r3{left:728px;background:var(--teal-bg);border-color:var(--teal)}
.r3 .st{color:var(--teal)}
.r4{left:956px;background:var(--gold-bg);border-color:var(--gold)}
.r4 .st{color:var(--gold)}
.word{position:absolute;left:274px;top:194px;width:676px;height:138px;border:1px solid var(--line);border-radius:6px;padding:20px 28px 0 28px}
.word h2{font-size:20px;font-weight:600;display:flex;align-items:center;gap:8px}
.word p{font-size:11.3px;line-height:16px;color:#333;margin-top:2px}
.word b{color:var(--ink)}
.exercise{position:absolute;left:956px;top:194px;width:221px;height:138px;background:var(--gold-bg);border-radius:6px}
.exercise .art{position:absolute;left:55px;top:-28px;width:120px;height:100px;border-radius:40px;background:radial-gradient(circle at 50% 55%,#f7c744,#f3d58a 60%,transparent 72%)}
.exercise .cta{position:absolute;left:0;right:0;top:90px;text-align:center;font-size:9px;font-weight:700;line-height:13px}
.sec-title{position:absolute;left:278px;font-size:19px;font-weight:600}
.chart{position:absolute;left:277px;top:379px}
.analysis{position:absolute;left:280px;top:744px;width:870px;font-size:11.3px;line-height:16px;color:#222}
</style>
</head>
<body>
<aside class="sidebar">
  <div class="brand">WordNest Tutor</div>
  <svg class="brand-ext" width="13" height="13" viewBox="0 0 13 13" fill="none" stroke="#fff" stroke-width="1.5"><path d="M6 2H1.5v9.5H11V7M8 1.5h3.5V5M11.5 1.5 6 7"/></svg>
  <div class="nav-active">WordNest Tutor
    <svg width="14" height="13" viewBox="0 0 14 13"><path d="M7 0 0 6h2v7h4V9h2v4h4V6h2z" fill="#f2b21d"/></svg></div>
  <div class="filter"><span>All</span><svg width="10" height="7" viewBox="0 0 10 7"><path d="M1 1l4 4 4-4" stroke="#fff" stroke-width="1.6" fill="none"/></svg></div>
  <div class="group" style="top:191px"><h3>Short-Term Memory<span class="qmark">?</span></h3><div class="cur">GRAB</div></div>
  <div class="group" style="top:242px"><h3>Working Memory<span class="qmark">?</span></h3>
    <ul><li>Cool Down</li><li>Crav</li><li>Go For</li><li>Go-To</li><li>In The Mood For</li><li>Sip</li><li>Soothing</li><li>Stick With</li><li>Throw In/Throw On</li></ul></div>
  <div class="group" style="top:438px"><h3>Long-Term Memory<span class="qmark">?</span></h3><div class="sub">Give ItA Try</div></div>
  <div class="extra" style="top:501px"><svg width="14" height="18" viewBox="0 0 14 18"><path d="M7 0a7 7 0 0 0-7 7c0 5 7 11 7 11s7-6 7-11a7 7 0 0 0-7-7z" fill="#f2b21d"/><circle cx="7" cy="7" r="2.6" fill="#2a1f33"/></svg>Daily English</div>
  <div class="extra" style="top:536px"><svg width="14" height="16" viewBox="0 0 14 16"><rect x="1" y="1" width="12" height="15" fill="#f2b21d"/><g fill="#2a1f33"><rect x="3" y="3" width="2" height="2"/><rect x="6" y="3" width="2" height="2"/><rect x="9" y="3" width="2" height="2"/><rect x="3" y="7" width="2" height="2"/><rect x="6" y="7" width="2" height="2"/><rect x="9" y="7" width="2" height="2"/><rect x="5.5" y="11" width="3" height="5"/></g></svg>Business</div>
</aside>

<div class="topbar">
  <svg width="16" height="16" viewBox="0 0 16 16" fill="none" stroke="#222" stroke-width="1.4"><circle cx="8" cy="8" r="6.8"/><path d="M5 8.2l2 2 4-4"/></svg>
  <svg width="17" height="17" viewBox="0 0 24 24" fill="none" stroke="#222" stroke-width="1.8"><circle cx="12" cy="12" r="3.2"/><path d="M12 2v3M12 19v3M2 12h3M19 12h3M4.9 4.9l2.1 2.1M17 17l2.1 2.1M4.9 19.1 7 17M17 7l2.1-2.1"/><circle cx="12" cy="12" r="7"/></svg>
  <svg width="17" height="17" viewBox="0 0 24 24" fill="none" stroke="#222" stroke-width="1.8"><path d="M6 17V11a6 6 0 0 1 12 0v6l2 2H4z"/><path d="M10 21h4"/></svg>
  <div class="avatar">S</div>
  <svg width="9" height="6" viewBox="0 0 10 7"><path d="M1 1l4 4 4-4" stroke="#222" stroke-width="1.6" fill="none"/></svg>
</div>

<div class="review r1"><div class="lbl">REVIEW 1</div><div class="st">Completed</div><div class="bar"><i style="width:118px;background:var(--purple)"></i></div>
  <div class="dot"><svg width="18" height="18" viewBox="0 0 18 18"><circle cx="9" cy="9" r="9" fill="#6a4fc8"/><path d="M5 9.3l2.7 2.6L13 6.5" stroke="#fff" stroke-width="2" fill="none"/></svg></div></div>
<div class="review r2"><div class="lbl">REVIEW 2</div><div class="st">You are here</div><div class="bar"><i style="width:46px;background:var(--orange)"></i></div>
  <div class="dot"><svg width="14" height="16" viewBox="0 0 14 16"><circle cx="7" cy="4" r="3.5" fill="#f07a3f"/><path d="M0 16a7 7 0 0 1 14 0z" fill="#f07a3f"/></svg></div></div>
<div class="review r3"><div class="lbl">REVIEW 3</div><div class="st">Unvisited</div><div class="bar"></div><div class="dot"></div></div>
<div class="review r4"><div class="lbl">REVIEW 4</div><div class="st">Unvisited</div><div class="bar"></div><div class="dot"></div></div>

<section class="word">
  <h2>Grab <svg width="20" height="19" viewBox="0 0 20 19"><path d="M10 0l3 6.2 6.8.9-5 4.7 1.3 6.7L10 15.3 3.9 18.5l1.3-6.7-5-4.7L7 6.2z" fill="#f2b21d"/></svg></h2>
  <p>The word <b>"grab"</b> is most commonly used as a <b>verb,</b> meaning <b>to take something quickly or suddenly</b>. Imagine you're running late for school. You don't have time for breakfast, so you quickly <b>grab</b> an apple from the kitchen and rush out the door. As you reach the bus stop, your friend waves &amp; says, "Hey! Let's <b>grab</b> a coffee after class." Later, when you sit down, your phone starts ringing. You <b>grab</b> it from your bag and answer.</p>
</section>

<section class="exercise">
  <div class="art" role="img" aria-label="Illustration of a student reading a book surrounded by idea bulbs and gears"></div>
  <div class="cta">START VOCABULARY<br>REVIEW EXERCISE 3</div>
</section>

<h2 class="sec-title" style="top:343px">Learning Curve Graph</h2>

<svg class="chart" width="890" height="320" viewBox="0 0 890 320" font-family="Poppins, sans-serif">
  <defs>
    <linearGradient id="g1" x1="0" x2="1"><stop offset="0" stop-color="#f2effd"/><stop offset="1" stop-color="#f2effd" stop-opacity="0"/></linearGradient>
    <linearGradient id="g2" x1="0" x2="1"><stop offset="0" stop-color="#ecf8ee"/><stop offset="1" stop-color="#ecf8ee" stop-opacity="0"/></linearGradient>
    <linearGradient id="g3" x1="0" x2="1"><stop offset="0" stop-color="#fdeee8"/><stop offset="1" stop-color="#fdeee8" stop-opacity="0"/></linearGradient>
    <linearGradient id="g4" x1="0" x2="1"><stop offset="0" stop-color="#e8f5fa"/><stop offset="1" stop-color="#e8f5fa" stop-opacity="0"/></linearGradient>
  </defs>
  <rect x="0" y="0" width="835" height="52" fill="url(#g1)"/>
  <rect x="0" y="55" width="835" height="115" fill="url(#g2)"/>
  <rect x="0" y="172" width="835" height="36" fill="url(#g3)"/>
  <rect x="0" y="209" width="835" height="36" fill="url(#g4)"/>
  <g font-size="11" fill="#666">
    <text x="15" y="30">Long-term Memory</text>
    <text x="15" y="118">Working Memory</text>
    <text x="15" y="194">Short-Term Memory</text>
    <text x="15" y="231">Forgotten Memory</text>
  </g>
  <line x1="0" y1="245" x2="889" y2="245" stroke="#ccc"/>
  <g stroke="#bbb">
    <line x1="17" y1="260" x2="17" y2="272"/><line x1="888" y1="258" x2="888" y2="270"/>
    <line x1="67" y1="245" x2="67" y2="256"/><line x1="119" y1="245" x2="119" y2="256"/><line x1="170" y1="245" x2="170" y2="256"/><line x1="221" y1="245" x2="221" y2="256"/><line x1="271" y1="245" x2="271" y2="256"/><line x1="322" y1="245" x2="322" y2="256"/><line x1="372" y1="245" x2="372" y2="256"/><line x1="424" y1="245" x2="424" y2="256"/><line x1="474" y1="245" x2="474" y2="256"/><line x1="524" y1="245" x2="524" y2="256"/><line x1="575" y1="245" x2="575" y2="256"/><line x1="626" y1="245" x2="626" y2="256"/><line x1="676" y1="245" x2="676" y2="256"/><line x1="727" y1="245" x2="727" y2="256"/><line x1="778" y1="245" x2="778" y2="256"/>
  </g>
  <g font-size="9.5" fill="#333" text-anchor="middle">
    <text x="17" y="282">18 May</text><text x="70" y="282">12:00</text><text x="122" y="282">19 May</text><text x="174" y="282">12:00</text><text x="226" y="282">20 May</text><text x="279" y="282">12:00</text><text x="331" y="282">21 May</text><text x="383" y="282">12:00</text><text x="435" y="282">22 May</text><text x="487" y="282">12:00</text><text x="540" y="282">23 May</text><text x="592" y="282">12:00</text><text x="644" y="282">24 May</text><text x="696" y="282">12:00</text><text x="748" y="282">25 May</text><text x="801" y="282">12:00</text><text x="853" y="282">26 May</text>
  </g>
  <text x="458" y="313" font-size="10" font-weight="500" text-anchor="middle">DATE RANGE</text>
  <path d="M323 190 C370 190 410 215 421 245" fill="none" stroke="#555" stroke-width="1.3" stroke-dasharray="1.5 3"/>
  <path d="M425 79 C540 79 624 140 626 245" fill="none" stroke="#555" stroke-width="1.3" stroke-dasharray="1.5 3"/>
  <rect x="319" y="190" width="8" height="55" rx="4" fill="#1a1025"/>
  <rect x="421" y="79" width="8" height="166" rx="4" fill="#1a1025"/>
  <rect x="299" y="163" width="48" height="19" rx="3" fill="#fff" stroke="#e6e6e6"/>
  <text x="323" y="176" font-size="9" text-anchor="middle">21 May</text>
  <rect x="401" y="44" width="48" height="19" rx="3" fill="#fff" stroke="#e6e6e6"/>
  <text x="425" y="57" font-size="9" text-anchor="middle">22 May</text>
</svg>

<h2 class="sec-title" style="top:706px;left:280px">WordNest Tutor Learning Analysis</h2>
<p class="analysis">Lorem ipsum <b>dolor</b> sit amet, consectetur adipiscing elit. Nam <b>rutrum commodo</b> enim id bibendum. Nunc dignissim risus <b>dolor</b>nec finibus dictum eu. Aliquam sit amet euismod metus, quis malesuada erat. Sed at felis quis nulla feugiat cursus at at <b>dolor</b>. Maecenas pretium alquet dapibus. Fusce et eleifend massa.&nbsp; Sed convallis ex mi, at lobortis ligula congue vel.</p>
</body>
</html>
```